Business Card Design Project

We need a Business Card for an Mechanical Engineering firm in Singapore. The design should be Modern & Technical looking, yet eye catching.

Our company deals in Cutting Tools & Machine Accessories for the Manufacturing Industries such as Oil & Gas, Aero Space, etc... For more information on our Company, you can either email me or view our website www.torvalen.com.sg.

We are trying to revamp our image to give our consumers a fresh new perspective to our company, so we welcome all ideas.

Industry/Entity Type

Business

Requirements
Must have
• Must incorporate New Company Logo into the card as shown in Uploaded file.

```html
<!DOCTYPE html>
<html lang="en">
<head>
<meta charset="utf-8">
<title>Torvalen Tools – Business Card</title>
<link rel="stylesheet" href="https://fonts.googleapis.com/css2?family=Questrial&display=swap">
<style>
  :root {
    --bg: #a9b296;
    --maroon: #8c0030;
    --rose: #b0104a;
    --ink: #2a2a2a;
    --paper: #ffffff;
  }
  * { margin: 0; padding: 0; box-sizing: border-box; }
  html, body { width: 1200px; height: 900px; overflow: hidden; }
  body {
    position: relative;
    background: var(--bg);
    font-family: "Questrial", "Century Gothic", sans-serif;
  }
  .card {
    position: absolute;
    top: 200px;
    width: 300px;
    height: 500px;
    border-radius: 26px;
    box-shadow: 0 6px 14px rgba(0,0,0,0.28);
    overflow: hidden;
  }
  .card-front { left: 230px; background: var(--maroon); }
  .card-back  { left: 670px; background: var(--paper); }

  .brand {
    position: absolute;
    left: 50%;
    top: 50%;
    transform: translate(-50%, -50%);
    display: flex;
    align-items: center;
    gap: 10px;
    white-space: nowrap;
  }
  .brand-dot {
    flex: 0 0 auto;
    width: 26px; height: 26px; border-radius: 50%;
    background: var(--paper);
  }
  .brand-name {
    color: var(--paper);
    font-size: 20px;
    letter-spacing: 2px;
  }

  .contact {
    position: absolute;
    left: 32px;
    top: 40px;
    font-size: 16px;
    line-height: 21px;
    color: var(--ink);
    white-space: nowrap;
  }
  .contact .name { color: var(--maroon); font-size: 19px; font-weight: bold; }
  .contact .role { margin-bottom: 4px; }
  .contact .company, .contact .label, .contact .web { color: var(--rose); }

  .back-mark {
    position: absolute;
    left: 32px;
    bottom: 48px;
    display: flex;
    align-items: center;
    gap: 8px;
    white-space: nowrap;
  }
  .back-mark .dot { flex: 0 0 auto; width: 22px; height: 22px; border-radius: 50%; background: var(--maroon); }
  .back-mark .word { color: var(--maroon); font-size: 16px; letter-spacing: 1px; }
</style>
</head>
<body>
  <section class="card card-front" aria-label="Card front">
    <div class="brand">
      <span class="brand-dot"></span>
      <span class="brand-name">TORVALEN TOOLS</span>
    </div>
  </section>

  <section class="card card-back" aria-label="Card back">
    <div class="contact">
      <p class="name">Marcus Lim</p>
      <p class="role">Manager</p>
      <p class="company">Torvalen Tools Pte Ltd.</p>
      <p>27 Kallang Way #03-12</p>
      <p>Kallang Trade Centre</p>
      <p>Singapore 349210</p>
      <p><span class="label">tel:</span> 656 902 3148</p>
      <p><span class="label">mob:</span> 987 210 4563</p>
      <p><span class="label">fax:</span> 656 902 3149</p>
      <p>hello@torvalen.com.sg</p>
      <p class="web">www.torvalen.com.sg</p>
    </div>
    <div class="back-mark">
      <span class="dot"></span>
      <span class="word">TORVALEN</span>
    </div>
  </section>
</body>
</html>
```